Kestrel Facilities Business Card Design

We would now like to design business cards with the new Kestrel Facilities logo

Target Market(s)

Professional

Industry/Entity Type

Professional services

Contact Information for Business Card

Employee name, title, phone number, email address, corporate office address and logo.

Font styles to use
Sans Serif

Colors
0054AA
0677BA
7BADD7
CADEEF
E8F1F8

Requirements
Must have
• My logo
Should not have
• any other pictures or images besides my logo

```html
<!DOCTYPE html>
<html lang="en">
<head>
<meta charset="utf-8">
<title>Kestrel Facilities – Business Card</title>
<link rel="stylesheet" href="https://fonts.googleapis.com/css2?family=Oswald:wght@500;600&family=Lato:wght@400&display=swap">
<style>
  :root {
    --stage: #2b2b2b;
    --paper: #ffffff;
    --brand-blue: #1a7fe2;
    --brand-blue-deep: #0677ba;
    --pattern-light: #3b93ea;
    --ink: #1c1c1c;
    --rule: #9a9a9a;
  }
  * { margin: 0; padding: 0; box-sizing: border-box; }
  html, body { width: 1200px; height: 1108px; overflow: hidden; }
  body {
    background: var(--stage);
    display: flex;
    align-items: center;
    justify-content: center;
    gap: 60px;
  }
  .card {
    width: 420px;
    height: 700px;
    border-radius: 26px;
    position: relative;
    overflow: hidden;
  }
  .card-front {
    background: var(--paper);
    display: flex;
    flex-direction: column;
    align-items: center;
    text-align: center;
  }
  .wordmark {
    margin-top: 120px;
    display: flex;
    align-items: center;
    gap: 16px;
    font-family: 'Oswald', sans-serif;
    font-weight: 600;
    font-size: 46px;
    line-height: 1.0;
    text-transform: uppercase;
    color: var(--brand-blue);
    text-align: left;
  }
  .wordmark-square {
    width: 92px;
    height: 92px;
    background: var(--brand-blue);
    flex-shrink: 0;
  }
  .holder-name {
    margin-top: 92px;
    font-family: 'Oswald', sans-serif;
    font-weight: 500;
    font-size: 36px;
    letter-spacing: 0.2px;
    text-transform: uppercase;
    color: var(--brand-blue);
    line-height: 1.1;
  }
  .holder-title {
    font-family: 'Lato', sans-serif;
    font-size: 19px;
    color: var(--ink);
    margin-top: 2px;
  }
  .icon-rule {
    display: flex;
    align-items: center;
    gap: 8px;
    width: 300px;
    margin-top: 16px;
  }
  .icon-rule .rule { flex: 1; height: 1px; background: var(--rule); }
  .icon-box {
    width: 26px; height: 26px;
    border-radius: 4px;
    background: var(--brand-blue);
    display: flex; align-items: center; justify-content: center;
  }
  .contact-list {
    list-style: none;
    margin-top: 12px;
    font-family: 'Lato', sans-serif;
    font-size: 19px;
    line-height: 1.4;
    color: var(--ink);
  }
  .contact-list .accent { color: var(--brand-blue); }
  .divider { width: 300px; height: 1px; background: var(--rule); margin-top: 12px; }
  .address {
    font-family: 'Lato', sans-serif;
    font-style: normal;
    font-size: 19px;
    line-height: 1.4;
    color: var(--ink);
    margin-top: 12px;
  }
  .card-back {
    background: var(--brand-blue);
  }
  .back-pattern {
    position: absolute;
    inset: 0;
    background: linear-gradient(160deg, var(--pattern-light) 0%, var(--brand-blue) 55%, var(--brand-blue-deep) 100%);
  }
  .back-mark {
    position: absolute;
    right: 70px;
    bottom: 110px;
    display: flex;
    align-items: center;
    gap: 8px;
    font-family: 'Oswald', sans-serif;
    font-weight: 600;
    font-size: 20px;
    text-transform: uppercase;
    color: var(--paper);
  }
  .back-mark-square { width: 18px; height: 18px; background: var(--paper); }
</style>
</head>
<body>
  <section class="card card-front">
    <div class="wordmark">
      <span class="wordmark-square"></span>
      <span>Kestrel<br>Facilities</span>
    </div>
    <h1 class="holder-name">Daniel Hartley</h1>
    <p class="holder-title">Managing Director</p>
    <div class="icon-rule">
      <span class="rule"></span>
      <span class="icon-box">
        <svg width="16" height="16" viewBox="0 0 16 16" aria-hidden="true"><path d="M2 5c0-2 2-3 6-3s6 1 6 3v1h-3V5H5v1H2z M4 8h8l1 5H3z" fill="#fff"/></svg>
      </span>
      <span class="icon-box">
        <svg width="16" height="16" viewBox="0 0 16 16" aria-hidden="true"><rect x="1.5" y="3.5" width="13" height="9" fill="none" stroke="#fff" stroke-width="1.4"/><path d="M1.5 3.5 8 9l6.5-5.5" fill="none" stroke="#fff" stroke-width="1.4"/></svg>
      </span>
      <span class="icon-box">
        <svg width="16" height="16" viewBox="0 0 16 16" aria-hidden="true"><circle cx="8" cy="8" r="6" fill="#fff"/><path d="M5 5c2 0 2 2 4 2s1 3-1 3-1 3-3 2" fill="none" stroke="#1a7fe2" stroke-width="1.2"/></svg>
      </span>
      <span class="rule"></span>
    </div>
    <ul class="contact-list">
      <li>044-987 650 312</li>
      <li>hello@kestrelfac.com</li>
      <li>www.<span class="accent">kestrelfac</span>.com</li>
    </ul>
    <div class="divider"></div>
    <address class="address">88 Harbour Lane<br>20417, Northfield</address>
  </section>

  <section class="card card-back">
    <div class="back-pattern" role="img" aria-label="Repeating embossed brand-mark pattern in blue tones"></div>
    <div class="back-mark">
      <span class="back-mark-square"></span>
      <span>Kestrel Facilities</span>
    </div>
  </section>
</body>
</html>
```